urine drug test box

Need a urine drug test kit box designed for shelves of pharmacies and chemists.
"Pellumark" is the brand
I would like the pictures of the drug test on the front.
Must say on the front of box below,
Pellumark 8 Panel Dip Card (PLM-08)
8 Drugs Tested
Marijuana THC
Cocaine COC
Amphetamine AMP
Methamphetamine MET
Benzodiazepine BZO
Opiates OPI
Methylenedioxymethamphetamine MDMA
K2 (Synthetic Marijuana)
Contains 3 single-use drug test kits
Results in just 5 minutes
Complies to Australian Standards AS4308:2008
Back of box I'd like this statement,
Results are just a guide only. Like all drug testing devices…non-negative results must be confirmed in a lab by gas chromatography/mass spectrometry (GC/MS)
Store at any temperature from 2°C to 30°C
Avoid direct sunlight
Manufactured by Quindle (logo uploaded)
Quindle.com.au
(I would like the picture of the procedure on the back. This picture is on the product procedure I have uploaded)
On the bottom side I'd like the barcode I have uploaded.
On the sides, and top I'd like the pellumark logo
home drug test kit. People that need to know quickly

```html
<!DOCTYPE html>
<html lang="en">
<head>
<meta charset="utf-8">
<title>Pellumark Urine Drug Test – Box Panels</title>
<link href="https://fonts.googleapis.com/css2?family=Montserrat:ital,wght@0,700;0,800;1,700;1,800;1,900&family=Roboto+Condensed:ital,wght@0,700;1,400&display=swap" rel="stylesheet">
<style>
  :root{
    --stage:#d0e1e9;
    --paper:#ffffff;
    --brand-blue:#2b9ad8;
    --sky-blue:#4cc3e8;
    --deep-blue:#1d86c8;
    --ink:#1c1c1c;
    --card-grey:#e9e8e2;
  }
  *{margin:0;padding:0;box-sizing:border-box}
  html,body{width:1200px;height:840px;overflow:hidden;background:var(--stage)}
  .stage{position:relative;width:1200px;height:840px;font-family:"Montserrat",sans-serif;color:var(--ink)}
  .panel{position:absolute;background:var(--paper);overflow:hidden;box-shadow:0 10px 26px rgba(40,80,100,.16)}

  /* main face */
  .box-top{left:300px;top:30px;width:440px;height:650px}
  .swoosh{position:absolute;inset:0;width:100%;height:100%}
  .brand-name{
    position:absolute;top:34px;right:30px;display:flex;align-items:center;gap:10px;
    font-weight:800;font-size:50px;letter-spacing:-1px;color:var(--brand-blue);
  }
  .brand-name .dot{width:14px;height:14px;border-radius:50%;background:var(--brand-blue)}
  .product-title{
    position:absolute;top:108px;right:30px;font-weight:900;font-style:italic;
    font-size:33px;letter-spacing:-.5px;white-space:nowrap;
  }
  .product-sub{
    position:absolute;top:150px;right:34px;font-weight:700;font-style:italic;font-size:13px;white-space:nowrap;
  }
  .drugs-pill{
    position:absolute;top:180px;left:92px;background:var(--brand-blue);color:#fff;
    font-weight:800;font-style:italic;font-size:19px;padding:5px 20px 5px 22px;border-radius:0 20px 20px 0;
  }
  .drug-list{
    position:absolute;top:222px;left:96px;list-style:none;
    font-family:"Roboto Condensed",sans-serif;font-style:italic;font-size:15px;line-height:19px;
  }
  .drug-list li::before{content:"- "}
  .kits-band{
    position:absolute;top:388px;left:170px;right:0;background:var(--deep-blue);color:#fff;
    font-weight:800;font-style:italic;font-size:18px;line-height:23px;padding:8px 14px 8px 20px;
  }
  .test-card{
    position:absolute;left:22px;top:410px;width:150px;height:104px;border-radius:6px;
    background:linear-gradient(135deg,#f1f0ea,var(--card-grey));
    box-shadow:0 4px 10px rgba(0,0,0,.25);
  }
  .result-badge{
    position:absolute;left:232px;top:478px;width:118px;height:118px;border-radius:50%;
    border:5px solid var(--deep-blue);background:#fff;display:flex;align-items:center;justify-content:center;
    text-align:center;color:var(--deep-blue);font-weight:800;font-style:italic;font-size:15px;line-height:18px;
  }
  .maker-name{
    position:absolute;left:22px;top:560px;display:flex;align-items:center;gap:8px;
    color:#fff;font-weight:800;font-size:20px;
  }
  .maker-name .dot{width:16px;height:16px;border-radius:50%;background:#fff}
  .compliance{
    position:absolute;right:14px;bottom:14px;font-family:"Roboto Condensed",sans-serif;
    font-weight:700;font-size:12px;color:var(--ink);white-space:nowrap;
  }

  /* long side */
  .box-side{left:740px;top:30px;width:130px;height:650px}
  .side-brand{
    position:absolute;left:50%;top:50%;transform:translate(-50%,-50%) rotate(-90deg);
    display:flex;align-items:center;gap:12px;white-space:nowrap;
    font-weight:800;font-size:62px;letter-spacing:-1px;color:var(--brand-blue);
  }
  .side-brand .dot{width:16px;height:16px;border-radius:50%;background:var(--brand-blue)}

  /* end side */
  .box-end{left:300px;top:680px;width:440px;height:130px}
  .end-brand{
    position:absolute;left:150px;top:50%;transform:translateY(-50%);
    display:flex;align-items:center;gap:10px;
    font-weight:800;font-size:46px;letter-spacing:-1px;color:var(--brand-blue);
  }
  .end-brand .dot{width:13px;height:13px;border-radius:50%;background:var(--brand-blue)}
</style>
</head>
<body>
<main class="stage">
  <section class="panel box-top">
    <svg class="swoosh" viewBox="0 0 440 650" preserveAspectRatio="none" aria-hidden="true">
      <path d="M0 0 L70 0 C100 220 170 470 330 650 L0 650 Z" fill="var(--sky-blue)"/>
      <path d="M0 0 L34 0 C62 250 128 480 265 650 L0 650 Z" fill="var(--brand-blue)" opacity=".35"/>
      <path d="M54 0 C86 235 158 475 306 650" fill="none" stroke="var(--deep-blue)" stroke-width="12"/>
    </svg>

    <div class="brand-name"><span class="dot"></span>Pellumark</div>
    <h1 class="product-title">URINE DRUG TEST</h1>
    <p class="product-sub">Pellumark 8 Panel Dip Card (PLM-08)</p>

    <div class="drugs-pill">8 DRUGS TESTED</div>
    <ul class="drug-list">
      <li>Marijuana THC</li>
      <li>Cocaine COC</li>
      <li>Amphetamine AMP</li>
      <li>Methamphetamine MET</li>
      <li>Benzodiazepine BZO</li>
      <li>Opiates OPI</li>
      <li>Methylenedioxymethamphetamine MDMA</li>
      <li>K2 (Synthetic Marijuana)</li>
    </ul>

    <div class="kits-band">CONTAINS 3 SINGLE-USE<br>DRUG TEST KITS</div>

    <div class="test-card" role="img" aria-label="Photo of the 8 panel dip card test device"></div>

    <div class="result-badge">Results in just<br>5 minutes</div>

    <div class="maker-name"><span class="dot"></span>Ardena Test</div>
    <p class="compliance">Complies to Australian Standards AS4308:2008</p>
  </section>

  <section class="panel box-side">
    <div class="side-brand"><span class="dot"></span>Pellumark</div>
  </section>

  <section class="panel box-end">
    <svg class="swoosh" viewBox="0 0 440 130" preserveAspectRatio="none" aria-hidden="true">
      <path d="M0 0 L130 0 C110 50 80 95 40 130 L0 130 Z" fill="var(--sky-blue)"/>
      <path d="M112 0 C95 50 66 95 26 130" fill="none" stroke="var(--deep-blue)" stroke-width="8"/>
    </svg>
    <div class="end-brand"><span class="dot"></span>Pellumark</div>
  </section>
</main>
</body>
</html>
```